Counseling Practice Business Card

I need a professional looking business card incorporating my new logo that was just completed. Card needs to incorporate my name and title, description of my specialty, my address, my phone number, my fax number, my email and my website URL. I need to be able to choose design on/with different paper colors and textures.
I do not have a lot of business card ideas so I am open to anything but I want bold,sharp, clear card without additional designs other than my logo (see attached file info). I am open to different color backgrounds or paper colors including black. I do not like traditional brackets around area codes in phone number or dashes between numbers in phone number. Am open to other ways of presenting including periods between numbers as appropriate. I do not know enough to know what I like yet but I want card to coordinate and work together with my logo. My practice emphasizes natural mental health interventions so any use of color (with background paper color or the blue and green in my logo) that elicits nature is nice. In addition to black, any natural brown or wood looking background might be desirable also. Most of the offerings so far look very similar and boring.

Target Market(s)

Potential therapy clients and other professionals

Contact Information for Business Card

Card information:
Gerald M. Whitcombe, Ph.D.
Licensed Clinical Psychologist
Integrative Health Coach
4812 Marlowe Ridge Blvd SE
Suite 310
Fernvale, GA 30417
(770) 415-2983 phone
(770) 581-4096 fax
drgeraldwhitcombe@quillmarsh.net
brightfernwellness.net

Font styles to use
Serif
Sans Serif
Other font styles liked:
• anything that you think looks crisp, clear and easily readable

Requirements
Must have
• Any color used should coordinate with my logo design (see attached files).
• Card should be printed horizontally so top and bottom are longest sides of rectangle.
• Background color or paper color should complement and highlight logo. Do not like a white background. black, grey, brown or any color my logo would blend well with.
Nice to have
• I would like designer to utilize color to highlight letters/name or phone-fax-web symbols.
• Bottom edge of card could be highlighted if appropriate to an idea.
Should not have
• I would NOT want the card to have a pure white background at all.
• No clear cards.
• Cards should be oriented with long sides on bottom and top, NOT sides. DO NOT LIKE THIS THIN TALL ORIENTATION.

```html
<!DOCTYPE html>
<html lang="en">
<head>
<meta charset="utf-8">
<title>Brightfern Wellness – Business Card</title>
<link href="https://fonts.googleapis.com/css2?family=Roboto:wght@300;400;500&family=Roboto+Condensed:wght@400;700&display=swap" rel="stylesheet">
<style>
  :root {
    --backdrop: #6e4d35;
    --card: #16181b;
    --brand-blue: #2a78bd;
    --brand-green: #1f8a3e;
    --text-light: #d4d6d8;
    --band-text: #c9dcef;
  }
  * { margin: 0; padding: 0; box-sizing: border-box; }
  html, body { width: 1200px; height: 960px; overflow: hidden; }
  body {
    position: relative;
    background: var(--backdrop);
    font-family: "Roboto", Arial, sans-serif;
  }
  .card {
    position: absolute;
    width: 600px;
    height: 343px;
    background: var(--card);
    box-shadow: 0 3px 8px rgba(0,0,0,0.45);
    overflow: hidden;
  }
  .card--front { left: 314px; top: 113px; }
  .card--back { left: 311px; top: 472px; }

  .wordmark {
    position: absolute;
    display: flex;
    align-items: center;
    gap: 10px;
    color: var(--brand-blue);
    font-family: "Roboto", Arial, sans-serif;
    font-weight: 500;
    line-height: 1;
    white-space: nowrap;
  }
  .wordmark__dot {
    border-radius: 50%;
    background: var(--brand-blue);
    flex: none;
  }
  .card--front .wordmark { left: 44px; top: 68px; font-size: 30px; }
  .card--front .wordmark__dot { width: 18px; height: 18px; }

  .address {
    position: absolute;
    left: 42px;
    top: 168px;
    color: var(--text-light);
    font-size: 14px;
    font-weight: 400;
    line-height: 18px;
    font-style: normal;
  }
  .contacts {
    position: absolute;
    left: 42px;
    top: 232px;
    list-style: none;
    color: var(--text-light);
    font-size: 14px;
    font-weight: 400;
  }
  .contacts li {
    display: flex;
    align-items: center;
    height: 19px;
    white-space: nowrap;
  }
  .contacts svg {
    width: 12px;
    height: 12px;
    margin-right: 12px;
    fill: var(--brand-blue);
  }

  .identity {
    position: absolute;
    right: 44px;
    top: 207px;
    text-align: right;
    font-family: "Roboto Condensed", Arial, sans-serif;
  }
  .identity__name {
    color: var(--brand-blue);
    font-size: 19px;
    font-weight: 700;
    text-transform: uppercase;
    letter-spacing: 0.2px;
    line-height: 24px;
  }
  .identity__role {
    color: var(--brand-green);
    font-size: 16px;
    font-weight: 400;
    line-height: 19px;
  }

  .card--back .wordmark {
    left: 0; right: 0; top: 120px;
    justify-content: center;
    font-size: 42px;
  }
  .card--back .wordmark__dot { width: 24px; height: 24px; }
  .web-band {
    position: absolute;
    left: 0; right: 0;
    top: 279px;
    height: 30px;
    background: var(--brand-blue);
    color: var(--band-text);
    font-size: 14px;
    font-weight: 400;
    letter-spacing: 4.2px;
    text-align: center;
    line-height: 30px;
  }
</style>
</head>
<body>

<section class="card card--front" aria-label="Business card front">
  <div class="wordmark"><span class="wordmark__dot"></span>Brightfern Wellness</div>

  <address class="address">
    4812 Marlowe Ridge Blvd SE<br>
    Suite 310<br>
    Fernvale, GA 30417
  </address>

  <ul class="contacts">
    <li>
      <svg viewBox="0 0 24 24" aria-hidden="true"><path d="M6.6 10.8a15.1 15.1 0 0 0 6.6 6.6l2.2-2.2c.3-.3.7-.4 1-.2 1.1.4 2.3.6 3.6.6.6 0 1 .4 1 1V20c0 .6-.4 1-1 1A17 17 0 0 1 3 4c0-.6.4-1 1-1h3.5c.6 0 1 .4 1 1 0 1.3.2 2.5.6 3.6.1.3 0 .7-.2 1z"/></svg>
      (770) 415-2983
    </li>
    <li>
      <svg viewBox="0 0 24 24" aria-hidden="true"><path d="M6 2h12v5H6zM3 8h18a1 1 0 0 1 1 1v8h-4v5H6v-5H2V9a1 1 0 0 1 1-1zm5 8v4h8v-4z"/></svg>
      (770) 581-4096
    </li>
    <li>
      <svg viewBox="0 0 24 24" aria-hidden="true"><path d="M2 5h20v14H2zm2 2v.5l8 5 8-5V7l-8 5z"/></svg>
      drgeraldwhitcombe@quillmarsh.net
    </li>
    <li>
      <svg viewBox="0 0 24 24" aria-hidden="true"><path d="M12 2a10 10 0 1 0 0 20 10 10 0 0 0 0-20zm-1 17.9A8 8 0 0 1 4.2 10.2L9 15v1a2 2 0 0 0 2 2zm6.9-2.5A2 2 0 0 0 16 16h-1v-3a1 1 0 0 0-1-1H8v-2h2a1 1 0 0 0 1-1V7h2a2 2 0 0 0 2-2v-.4a8 8 0 0 1 2.9 12.8z"/></svg>
      www.brightfernwellness.net
    </li>
  </ul>

  <div class="identity">
    <div class="identity__name">Gerald M. Whitcombe, Ph.D.</div>
    <div class="identity__role">Licensed Clinical Psychologist</div>
    <div class="identity__role">Integrative Health Coach</div>
  </div>
</section>

<section class="card card--back" aria-label="Business card back">
  <div class="wordmark"><span class="wordmark__dot"></span>Brightfern Wellness</div>
  <div class="web-band">www.brightfernwellness.net</div>
</section>

</body>
</html>
```